New Business Card for Web Design/Internet Marketing Company

Looking for a great looking new business card. We are a 10 year old web design, internet marketing and website management company that works mostly with small businesses.

Our new card needs to better match the colors and style of our website, be bold, extremely usable and slightly edgy.

Target Market(s)

Small/Medium businesses that have websites

Industry/Entity Type

Internet

Requirements
Must have
• Front and back design, full color, rounded corners please

Must use the colors/style of our website (JPG provided)

INFO FOR CARDS (as readable as possible please)
Mark Lenner
President/CEO
mark@trelvanmedia.example
Phone: 520-381-7459
Toll Free: 866-381-7459
Address: 4315 W. Calloway Ave. Ste. 140, Tucson, AZ 85792

THINGS I WANT TO PROMOTE (if there is room):
1. Our Website - www.trelvanmedia.example

2. Social Media
Twitter: @trelvanmedia
Facebook: www.facebook.com/trelvanmedia

3. Our Services
Web Design
Internet Marketing
Website Management

```html
<!DOCTYPE html>
<html lang="en">
<head>
<meta charset="utf-8">
<title>Trelvan Media — Business Card</title>
<link rel="stylesheet" href="https://fonts.googleapis.com/css2?family=Open+Sans:wght@400;600;700&display=swap">
<style>
  :root {
    --brand-blue: #2b87bd;
    --brand-blue-dark: #1d6b9c;
    --brand-orange: #f08a24;
    --card-white: #ffffff;
    --page-bg: #e4e6e8;
    --ink-white: #ffffff;
  }
  * { box-sizing: border-box; margin: 0; padding: 0; }
  html, body {
    width: 1200px; height: 944px; overflow: hidden;
    background: var(--page-bg);
    font-family: "Open Sans", Arial, sans-serif;
  }
  .card {
    position: absolute;
    width: 640px; height: 366px;
    border-radius: 14px;
    overflow: hidden;
    background: var(--card-white);
    box-shadow: 0 6px 18px rgba(0,0,0,.18);
  }
  /* Front */
  .card--front { left: 90px; top: 90px; display: flex; flex-direction: column; }
  .front__top {
    height: 110px; background: var(--brand-blue);
    display: flex; align-items: center; justify-content: center;
    color: var(--ink-white); font-size: 17px; letter-spacing: .5px;
  }
  .front__middle {
    height: 120px; display: flex; align-items: center; justify-content: center;
  }
  .front__bottom {
    flex: 1; background: var(--brand-blue);
    display: flex; align-items: center; justify-content: center;
    color: var(--ink-white); font-size: 19px; letter-spacing: .3px;
  }
  .bullet { margin: 0 8px; }
  .brand { display: flex; align-items: center; gap: 12px; }
  .brand__dot { width: 34px; height: 34px; border-radius: 50%; background: var(--brand-orange); }
  .brand__name { font-weight: 700; color: var(--brand-blue); font-size: 44px; letter-spacing: -.5px; }

  /* Back */
  .card--back { left: 470px; top: 470px; }
  .back__panel {
    position: absolute; left: 0; top: 0; width: 100%; height: 232px;
    background: var(--brand-blue); color: var(--ink-white);
  }
  .person { position: absolute; left: 30px; top: 24px; }
  .person__name { font-size: 25px; font-weight: 400; }
  .person__title { font-size: 16px; margin-top: 2px; }
  .address { position: absolute; left: 310px; top: 40px; display: flex; gap: 12px; font-size: 15px; line-height: 1.45; }
  .contacts { position: absolute; left: 310px; top: 112px; list-style: none; font-size: 15px; line-height: 1.45; }
  .contacts li { display: flex; align-items: center; gap: 12px; white-space: nowrap; }
  .icon { width: 16px; height: 16px; flex: none; fill: var(--ink-white); }
  .back__brand { position: absolute; left: 30px; top: 270px; }
  .back__brand .brand__name { font-size: 40px; }
  .back__brand .brand__dot { width: 30px; height: 30px; }
</style>
</head>
<body>

<section class="card card--front" aria-label="Business card front">
  <div class="front__top">www.trelvanmedia.example</div>
  <div class="front__middle">
    <div class="brand"><span class="brand__dot"></span><span class="brand__name">Trelvan Media</span></div>
  </div>
  <div class="front__bottom">
    Web Design<span class="bullet">•</span>Internet Marketing<span class="bullet">•</span>Website Management
  </div>
</section>

<section class="card card--back" aria-label="Business card back">
  <div class="back__panel">
    <div class="person">
      <p class="person__name">Mark Lenner</p>
      <p class="person__title">President/CEO</p>
    </div>
    <div class="address">
      <svg class="icon" viewBox="0 0 16 16" aria-hidden="true"><path d="M8 1 0 8h2v7h4v-5h4v5h4V8h2z"/></svg>
      <p>4315 W. Calloway Ave. Ste. 140<br>Tucson, AZ 85792</p>
    </div>
    <ul class="contacts">
      <li><svg class="icon" viewBox="0 0 16 16" aria-hidden="true"><path d="M1 3h14v10H1z M1 3l7 6 7-6" fill="none" stroke="#fff" stroke-width="1.6"/></svg>mark@trelvanmedia.example</li>
      <li><svg class="icon" viewBox="0 0 16 16" aria-hidden="true"><path d="M3 1h3l1.5 4-2 1.3a9 9 0 0 0 4.2 4.2L11 8.5l4 1.5v3a2 2 0 0 1-2 2A12 12 0 0 1 1 3a2 2 0 0 1 2-2z"/></svg>520-381-7459</li>
      <li><svg class="icon" viewBox="0 0 16 16" aria-hidden="true"><path d="M3 1h3l1.5 4-2 1.3a9 9 0 0 0 4.2 4.2L11 8.5l4 1.5v3a2 2 0 0 1-2 2A12 12 0 0 1 1 3a2 2 0 0 1 2-2z"/></svg>866-381-7459 (toll free)</li>
      <li><svg class="icon" viewBox="0 0 16 16" aria-hidden="true"><circle cx="8" cy="8" r="6"/></svg>@trelvanmedia</li>
      <li><svg class="icon" viewBox="0 0 16 16" aria-hidden="true"><rect x="2" y="2" width="12" height="12" rx="2"/></svg>www.friendlane.example/trelvanmedia</li>
    </ul>
  </div>
  <div class="brand back__brand"><span class="brand__dot"></span><span class="brand__name">Trelvan Media</span></div>
</section>

</body>
</html>
```